The Brandwell Firm

We need a new design for our letterhead and envelopes. We are a personal injury and criminal defense firm so we need something modern and clean, but more on the professional/traditional side. Our new logo has two colors and is attached to the file so we need something that works well with those colors/matches the design. The following information needs to be on the letterhead:
Phone: (555) 214-3370
Fax: (555) 214-5186
Toll-Free: (888) 431-2059
Post Office Box 4721
Millbrook, SC 29555-4721
HarmClaimCounsel.example
PalmettoTrialAdvocates.example

Target Market(s)

Clients, government agencies, other law firms

Industry/Entity Type

Legal

Font styles to use
Sans Serif
Other font styles liked:
• Arial

Colors

Designer to choose colors to be used in the design.

Requirements
Must have
• Must look professional and clean, modern
Nice to have
• I would like to see a design that works with the logo but does not distract from the content that will be printed on it
Should not have
• Too many colors or crazy designs.

```html
<!DOCTYPE html>
<html lang="en">
<head>
<meta charset="utf-8">
<title>The Brandwell Firm – Stationery</title>
<link rel="stylesheet" href="https://fonts.googleapis.com/css2?family=Open+Sans:wght@400;600&display=swap">
<style>
  :root {
    --backdrop: #5b5b5d;
    --paper: #ffffff;
    --brand-red: #d3322f;
    --brand-blue: #3d3c9c;
    --ink: #3a3a3a;
    --shadow: rgba(0,0,0,0.45);
  }
  html, body {
    margin: 0;
    padding: 0;
    width: 1200px;
    height: 904px;
    overflow: hidden;
    background: var(--backdrop);
    font-family: "Open Sans", Arial, sans-serif;
  }
  .canvas { position: relative; width: 1200px; height: 904px; }

  .sheet {
    position: absolute;
    background: var(--paper);
    box-shadow: 2px 3px 6px var(--shadow);
    overflow: hidden;
  }

  /* Brand name lockup */
  .brand {
    position: absolute;
    display: flex;
    align-items: center;
    gap: 5px;
    white-space: nowrap;
  }
  .brand-dot {
    width: 9px; height: 9px;
    border-radius: 50%;
    background: var(--brand-red);
    flex: none;
  }
  .brand-name {
    font-weight: 600;
    color: var(--brand-blue);
    font-size: 12px;
    letter-spacing: 0.2px;
    text-transform: uppercase;
  }

  /* Corner brand-mark area (placeholder block) */
  .corner-mark {
    position: absolute;
    background: linear-gradient(to bottom, var(--brand-red) 0%, var(--brand-red) 38%, var(--brand-blue) 44%, var(--brand-blue) 100%);
    opacity: 0.9;
  }

  /* Letterhead */
  .letterhead { left: 129px; top: 145px; width: 471px; height: 666px; }
  .letterhead .brand { left: 38px; top: 62px; }
  .letterhead .corner-mark { left: 392px; top: 453px; width: 72px; height: 213px; }
  .mailing-address {
    position: absolute;
    left: 230px; top: 43px;
    font-size: 7px;
    line-height: 10px;
    color: var(--ink);
    font-style: normal;
  }
  .header-divider {
    position: absolute;
    left: 323px; top: 44px;
    width: 1px; height: 47px;
    background: var(--ink);
  }
  .contact-list {
    position: absolute;
    left: 331px; top: 42px;
    margin: 0; padding: 0;
    list-style: none;
    font-size: 7px;
    line-height: 9.8px;
    color: var(--ink);
  }
  .contact-list li { display: flex; align-items: center; gap: 4px; }
  .contact-icon { width: 6px; height: 6px; flex: none; }

  /* Envelope front */
  .envelope-front { left: 630px; top: 278px; width: 486px; height: 243px; }
  .envelope-front .brand { left: 28px; top: 50px; }
  .envelope-front .corner-mark { left: 424px; top: 79px; width: 56px; height: 164px; }
  .return-address {
    position: absolute;
    left: 48px; top: 80px;
    font-size: 7px;
    line-height: 10px;
    color: var(--ink);
    text-align: center;
    font-style: normal;
  }

  /* Envelope back */
  .envelope-back { left: 630px; top: 556px; width: 486px; height: 244px; }
  .envelope-flap { position: absolute; left: 0; top: 0; width: 486px; height: 72px; }
  .envelope-back .brand { left: 50%; top: 28px; transform: translateX(-50%); }
  .envelope-back .brand-dot { background: var(--paper); width: 7px; height: 7px; }
  .envelope-back .brand-name { color: var(--paper); font-size: 10px; }
</style>
</head>
<body>
<main class="canvas">

  <section class="sheet letterhead" aria-label="Letterhead">
    <div class="brand">
      <span class="brand-dot"></span>
      <span class="brand-name">The Brandwell Firm</span>
    </div>
    <address class="mailing-address">
      Post Office Box 4721<br>
      Millbrook, SC 29555-4721
    </address>
    <div class="header-divider"></div>
    <ul class="contact-list">
      <li>
        <svg class="contact-icon" viewBox="0 0 6 6"><path d="M0.5 1.5 Q3 0 5.5 1.5 L5 2.5 L4 2 L2 2 L1 2.5 Z M1.3 3 H4.7 V5.5 H1.3 Z" fill="var(--brand-blue)"/></svg>
        (555) 214-3370
      </li>
      <li>
        <svg class="contact-icon" viewBox="0 0 6 6"><rect x="1.5" y="0.5" width="3" height="2" fill="var(--brand-blue)"/><rect x="0.5" y="2.5" width="5" height="3" rx="0.5" fill="var(--brand-blue)"/></svg>
        (555) 214-5186
      </li>
      <li>
        <svg class="contact-icon" viewBox="0 0 6 6"><path d="M1 0.5 L2.3 0.5 L2.8 2 L2 2.6 Q2.8 3.6 3.4 4 L4 3.2 L5.5 3.7 L5.5 5 Q2.5 5.5 1 0.5 Z" fill="var(--brand-blue)"/></svg>
        (888) 431-2059
      </li>
      <li>
        <svg class="contact-icon" viewBox="0 0 6 6"><circle cx="3" cy="3" r="2.6" fill="none" stroke="var(--brand-blue)" stroke-width="0.7"/><path d="M0.4 3 H5.6 M3 0.4 Q1.5 3 3 5.6 M3 0.4 Q4.5 3 3 5.6" fill="none" stroke="var(--brand-blue)" stroke-width="0.5"/></svg>
        HarmClaimCounsel.example
      </li>
      <li>
        <svg class="contact-icon" viewBox="0 0 6 6"><circle cx="3" cy="3" r="2.6" fill="none" stroke="var(--brand-blue)" stroke-width="0.7"/><path d="M0.4 3 H5.6 M3 0.4 Q1.5 3 3 5.6 M3 0.4 Q4.5 3 3 5.6" fill="none" stroke="var(--brand-blue)" stroke-width="0.5"/></svg>
        PalmettoTrialAdvocates.example
      </li>
    </ul>
    <div class="corner-mark" role="img" aria-label="Large brand mark in red and blue, bleeding off the bottom right corner"></div>
  </section>

  <section class="sheet envelope-front" aria-label="Envelope front">
    <div class="brand">
      <span class="brand-dot"></span>
      <span class="brand-name">The Brandwell Firm</span>
    </div>
    <address class="return-address">
      Post Office Box 4721<br>
      Millbrook, SC 29555-4721
    </address>
    <div class="corner-mark" role="img" aria-label="Large brand mark in red and blue, bleeding off the bottom right edge"></div>
  </section>

  <section class="sheet envelope-back" aria-label="Envelope back">
    <svg class="envelope-flap" viewBox="0 0 486 72" preserveAspectRatio="none">
      <path d="M0 0 H486 V8 Q486 40 446 44 L243 70 L40 44 Q0 40 0 8 Z" fill="var(--brand-blue)"/>
    </svg>
    <div class="brand">
      <span class="brand-dot"></span>
      <span class="brand-name">The Brandwell Firm</span>
    </div>
  </section>

</main>
</body>
</html>
```